Plakat-Design für kleine deutsche Immobilien- und Reiseveranstalter-Firma
Zielgruppe
Kleine deutsche Immobilien- und Reiseveranstalter-Firma, spezialisiert auf Italien. In Italien sind es Immobilienbesitzer, die aus versch. Gründen hoffen an Ausländer zu verkaufen/vermieten ( Alter ca. ab 35-40)
Aufgabenstellung
Um neue Immo-Besitzer anzusprechen, lassen wir in verschiedenen Gemeinden in der Nordtoskana Plakate gegen Gebühr kleben ( 70 x 100, meistens 1 bis 2 Wochen)
Text auf Italienisch
Was an Text rein muss( falls Sie es anders mitteilen wollen, bin ich gerne bereit es zu diskutieren)
VUOI VENDERE CASA A STRANIERI O AFFITTARLA A TURISTI ? (Übersetzung ca.:= wollen Sie Ihre Immobilie an Ausländer verkaufen oder an Touristen vermieten?)
Verdona
Germania – info@verdona-beispiel.de + 49 7412 3810457
Italia – 0571 – 394062, Cell.: 371 – 2094716, 335- 47 92608,
www.verdonacase-beispiel.com
www.verdonaaffitti-beispiel.com
Der Poster, den man meistens im Vorbeifahren sieht, soll springt sofort ins Auge , fast aufdringlich. Man kann mit Farben oder Bildern (oder beiden) arbeiten. Stechende Farben, sonst minimalistisch einfach. (??)
Erfahrung zeigt, daß die beiden Mobile Nummern (Cell.:) mehr sichtbar sein könnten. Ich kann zwei letzte zeigen, aber ungern, weil sie mir nicht gefallen und Neues – besseres suche.
PS: habe mal so was wie Guerilla -Marketing versucht – wurde nicht verstanden.
Bilder kann ich nach Wunsch liefern.

```html
<!DOCTYPE html>
<html lang="it">
<head>
<meta charset="utf-8">
<title>Verdona – Poster</title>
<link rel="stylesheet" href="https://fonts.googleapis.com/css2?family=Rubik:wght@300;400;700;800&display=swap">
<style>
  :root {
    --page-bg: #f2f2f0;
    --ink-white: #ffffff;
    --ink-dark: #1c1c1c;
    --brand-green: #2a9a3a;
    --street-sage: #7f978a;
    --wall-orange: #d2693f;
    --sky-blue: #8fb7c4;
    --ivy-green: #3f6f37;
    --facade-yellow: #e6c98b;
  }
  * { box-sizing: border-box; margin: 0; padding: 0; }
  html, body {
    width: 1146px; height: 1200px; overflow: hidden;
    background: var(--page-bg);
    font-family: "Rubik", sans-serif;
  }
  .poster {
    position: absolute; left: 163px; top: 20px;
    width: 820px; height: 1160px; overflow: hidden;
    box-shadow: 0 6px 18px rgba(0,0,0,.25);
  }
  .poster__photo {
    position: absolute; inset: 0;
    background:
      linear-gradient(180deg, rgba(127,151,138,0) 55%, var(--street-sage) 92%),
      linear-gradient(90deg, var(--wall-orange) 0%, #c8723f 24%, var(--sky-blue) 34%, #6f8fa0 52%, var(--ivy-green) 70%, var(--facade-yellow) 100%);
  }
  .headline {
    position: absolute; right: 79px; top: 290px;
    text-align: right; color: var(--ink-white);
    font-weight: 700; font-size: 52px; line-height: 63px;
    text-shadow: 2px 3px 4px rgba(0,0,0,.55);
    letter-spacing: .5px;
  }
  .contacts {
    position: absolute; left: 58px; top: 874px;
    color: var(--ink-white); font-weight: 300;
    font-size: 23px; line-height: 31px;
  }
  .contacts__country { font-weight: 800; }
  .contacts__group + .contacts__group { margin-top: 32px; }
  .contacts__indent { padding-left: 64px; }
  .brand {
    position: absolute; right: 45px; top: 968px;
    display: flex; align-items: center; gap: 10px;
  }
  .brand__dot {
    width: 26px; height: 26px; border-radius: 50%;
    background: var(--brand-green);
  }
  .brand__name {
    font-weight: 700; font-size: 58px; line-height: 1;
    color: var(--ink-dark);
  }
  .websites {
    position: absolute; right: 45px; top: 1060px;
    text-align: right; color: var(--ink-white);
    font-weight: 400; font-size: 24px; line-height: 32px;
  }
</style>
</head>
<body>
  <main class="poster">
    <div class="poster__photo" role="img" aria-label="Photo of a steep cobbled lane in an Italian lake village with colourful houses, a wall lantern, ivy and mountains over the lake"></div>

    <h1 class="headline">VUOI<br>VENDERE CASA<br>A STRANIERI<br>O AFFITTARLA<br>A TURISTI ?</h1>

    <section class="contacts">
      <div class="contacts__group">
        <p class="contacts__country">Germania</p>
        <p>info@verdona-beispiel.de</p>
        <p>+ 49 7412 3810457</p>
      </div>
      <div class="contacts__group">
        <p class="contacts__country">Italia</p>
        <p>0571 – 394062,</p>
        <p>Cell.: 371 – 2094716,</p>
        <p class="contacts__indent">335- 47 92608,</p>
      </div>
    </section>

    <div class="brand">
      <span class="brand__dot"></span>
      <span class="brand__name">Verdona</span>
    </div>

    <div class="websites">
      <p>www.verdonaaffitti-beispiel.com</p>
      <p>www.verdonacase-beispiel.com</p>
    </div>
  </main>
</body>
</html>
```